PixelHarbor Rangers (Ledgerline Nova)
A website dedicated to crypto education. We are a new company focused on blockchain edutainment (education and interesting and entertaining content about the blockchain space). We want a fun, clean/minimalist and modern website that is made up of an education platform which could be a website in it’s own right. It will be the reference point for our users/community for all of our other blockchain based content in the PHR website ecosystem which will be covering; crypto news, digital asset investing (including a technical and fundamental analysis subscription service), blockchain business solutions and an NFT section that will cover creative art projects (art, music, gaming and more). To feature a logins and payment system which may need a shopping basket set up for tutorial/educational platform that is accessed via the website, NFT page with sub-categories: education and NFT and metaverse/virtual world and merchandise shopping page which is Web 3.0 enabled (able to link to a VeloPurse, Kindle Vault etc , digital asset education page featuring blog and newsletter subscriptions links, A social media page where people can access videos, podcasts and our presence on other platforms such as Chirplo, Snapmora, Huddlex, Wirepost etc.
Number of Pages Required
5+ page
Look and feel

```html
<!DOCTYPE html>
<html lang="en">
<head>
<meta charset="utf-8">
<title>PixelHarbor Rangers – Light and Dark Home</title>
<link href="https://fonts.googleapis.com/css2?family=Poppins:wght@400;500;600;700&display=swap" rel="stylesheet">
<style>
:root{
  --stage:#d2d3d6;
  --navy:#0f2c63;
  --red:#a00d0d;
  --band:#2a4a85;
  --white:#ffffff;
}
*{box-sizing:border-box;margin:0;padding:0}
html,body{width:822px;height:1200px;overflow:hidden;background:var(--stage);font-family:"Poppins",sans-serif}
.page{position:absolute;top:30px;width:744px;height:2208px;transform:scale(.516);transform-origin:0 0;overflow:hidden;background:var(--bg)}
.page.light{left:18.6px;--bg:#ffffff;--heading:#0f2c63;--ink:#1b2340;--muted:#555b6b;--alt:#eef0f4;--price:#a00d0d;--outline:#0f2c63;--rule:#d6d8de;--input:#ffffff}
.page.dark{left:420px;--bg:#000000;--heading:#ffffff;--ink:#ffffff;--muted:#cfd2da;--alt:#141414;--price:#ffffff;--outline:#ffffff;--rule:#444;--input:#000000}
.abs{position:absolute}
.pixel-art{position:absolute;background:linear-gradient(180deg,#2a2a2a,#1a1a1a)}

/* hero */
.hero{position:absolute;left:0;top:0;width:744px;height:456px;color:var(--white)}
.hero-photo{position:absolute;inset:0;background:radial-gradient(ellipse at 55% 40%,#3e5687 0%,#1d2b4d 40%,#0b1020 80%)}
.brand{position:absolute;left:69px;top:16px;font-size:15px;font-weight:600;letter-spacing:.2px}
.account{position:absolute;right:74px;top:10px;display:flex;gap:10px;align-items:center;font-size:9px}
.account span{display:flex;align-items:center;gap:7px}
.ring{width:26px;height:26px;border:1px solid #fff;border-radius:50%;display:flex;align-items:center;justify-content:center}
.top-rule{position:absolute;left:69px;top:52px;width:606px;height:1px;background:rgba(255,255,255,.45)}
.nav{position:absolute;left:74px;top:67px;display:flex;font-size:9px;font-weight:500}
.nav a{color:#fff;text-decoration:none}
.nav i{font-style:normal;margin:0 22px}
.social-mini{position:absolute;right:72px;top:69px;display:flex;gap:6px}
.social-mini b,.dots b{width:8px;height:8px;border-radius:50%;background:currentColor;display:block}
.hero-band{position:absolute;left:0;top:360px;width:744px;height:96px;background:rgba(42,74,133,.85)}
.hero-title{position:absolute;left:67px;top:372px;font-size:29px;font-weight:700}
.hero-copy{position:absolute;left:69px;top:410px;width:320px;font-size:8.5px;line-height:18px}
.arrow{position:absolute;top:400px}
.btn{position:absolute;display:flex;align-items:center;justify-content:center;border-radius:20px;font-size:10px;font-weight:700;letter-spacing:.2px}
.btn.red{background:var(--red);color:#fff}
.btn.ghost{border:1.5px solid #fff;color:#fff}

/* sections */
.sec-title{position:absolute;left:0;width:744px;text-align:center;font-size:26px;font-weight:400;color:var(--heading)}
.sec-title strong{font-weight:700}
.sec-copy{position:absolute;text-align:center;font-size:8.5px;line-height:19px;color:var(--ink)}
.cards{position:absolute;left:68px;top:595px;display:flex;gap:8px}
.card{width:146px;height:225px;background:#fff;border:1px solid #e2e4ea;box-shadow:0 1px 4px rgba(0,0,0,.15);padding:4px;position:relative}
.card .pic{height:100px}
.card h3{font-size:9.5px;font-weight:400;color:#1b2340;margin:14px 6px 0;line-height:16px;height:34px}
.card p{font-size:7px;line-height:14px;color:#555b6b;margin:0 6px}
.card .more{position:absolute;left:10px;bottom:14px;width:60px;height:22px;border-radius:11px;background:var(--navy);color:#fff;font-size:7px;display:flex;align-items:center;justify-content:center}
.edu{position:absolute;left:0;top:870px;width:744px;height:265px;background:linear-gradient(90deg,#233f74,#2d4d8a 50%,#26457c);color:#fff}
.edu .sec-title{color:#fff;top:54px}
.nft-title{position:absolute;left:70px;top:1215px;font-size:26px;font-weight:400;color:var(--heading)}
.nft-title strong{font-weight:700}
.nft-copy{position:absolute;left:69px;top:1260px;width:300px;font-size:8.5px;line-height:17.5px;color:var(--ink)}
.btn.outline{border:1.5px solid var(--outline);color:var(--outline)}
.videos{position:absolute;left:0;top:1522px;width:744px;height:388px;background:var(--alt)}
.vcard{position:absolute;top:88px;width:196px}
.vcard .pic{height:152px;position:relative}
.play{position:absolute;left:83px;top:61px}
.vcard h4{font-size:10px;font-weight:400;line-height:17px;color:var(--ink);margin-top:12px}
.vcard p{font-size:7px;line-height:16px;color:var(--muted);margin-top:4px}
.vmeta{display:flex;justify-content:space-between;align-items:center;margin-top:8px;padding-right:14px}
.price{font-size:9.5px;font-weight:400;color:var(--price)}
.dots{display:flex;gap:7px;color:var(--ink)}
.dots b{width:7px;height:7px}

/* footer */
.footer{position:absolute;left:0;top:1910px;width:744px;height:298px;background:var(--bg);color:var(--ink)}
.fcol{position:absolute;top:66px;font-size:8px}
.fcol h5{font-size:9px;font-weight:600;letter-spacing:.2px}
.fcol h5:after{content:"";display:block;width:18px;height:1.5px;background:var(--muted);margin-top:7px;margin-bottom:13px}
.fcol li{list-style:none;line-height:18.5px}
.fcol .lab{font-size:8.5px;font-weight:500;line-height:14px}
.fcol .val{font-size:8px;line-height:14.5px;display:flex;gap:4px;align-items:flex-start}
.fcol .val svg{margin-top:3px;flex:none}
.news-input{position:absolute;left:504px;top:132px;width:172px;height:26px;border:1px solid var(--rule);border-radius:13px;background:var(--input);font-size:7px;padding-left:12px;display:flex;align-items:center;color:var(--muted)}
.news-input i{position:absolute;right:10px;top:7px;width:12px;height:12px;border-radius:50%;background:var(--red)}
.page.dark .news-input i{background:#2a5bd7}
.frule{position:absolute;left:69px;top:228px;width:606px;height:1px;background:var(--rule)}
.copy{position:absolute;left:72px;top:253px;font-size:8px}
.pay{position:absolute;left:308px;top:252px;display:flex;gap:5px}
.pay b{width:22px;height:13px;border-radius:2px;display:block}
.fsocial{position:absolute;right:72px;top:254px;display:flex;gap:10px;color:var(--ink)}
.fsocial b{width:10px;height:10px;border-radius:50%;background:currentColor;display:block}
</style>
</head>
<body>

<!-- LIGHT THEME PAGE -->
<div class="page light">
  <section class="hero">
    <div class="hero-photo" role="img" aria-label="Smiling young man in glasses and denim jacket at a café table with flowers"></div>
    <div class="brand">PixelHarbor Rangers</div>
    <div class="account">
      <span><span class="ring"><svg width="10" height="10" viewBox="0 0 10 10"><circle cx="5" cy="3" r="2.2" fill="#fff"/><path d="M1 10c0-3 8-3 8 0z" fill="#fff"/></svg></span>LOGIN</span>
      <span><span class="ring"><svg width="10" height="10" viewBox="0 0 10 10"><path d="M0 1h2l1.5 5h5L10 3H3" fill="none" stroke="#fff" stroke-width="1.2"/><circle cx="4" cy="8.5" r="1" fill="#fff"/><circle cx="8" cy="8.5" r="1" fill="#fff"/></svg></span>CART</span>
    </div>
    <div class="top-rule"></div>
    <nav class="nav"><a>HOME</a><i>|</i><a>ABOUT US</a><i>|</i><a>PHR ECOSYSTEM</a><i>|</i><a>BLOG</a><i>|</i><a>CONTACT</a></nav>
    <div class="social-mini" style="color:#fff"><b></b><b></b><b></b><b></b></div>
    <div class="hero-band"></div>
    <svg class="arrow" style="left:22px" width="20" height="16" viewBox="0 0 20 16"><path d="M19 8H3M8 3L3 8l5 5" stroke="#fff" stroke-width="2" fill="none"/></svg>
    <svg class="arrow" style="left:700px" width="20" height="16" viewBox="0 0 20 16"><path d="M1 8h16M12 3l5 5-5 5" stroke="#fff" stroke-width="2" fill="none"/></svg>
    <div class="hero-title">PixelHarbor Rangers</div>
    <p class="hero-copy">Lorem ipsum dolor sit amet, consectetur adipiscing elit, sed do eiusmod tempor incididunt ut labore et dolore magna aliqua.</p>
    <div class="btn red" style="left:425px;top:390px;width:120px;height:36px">GET STARTED</div>
    <div class="btn ghost" style="left:551px;top:390px;width:120px;height:36px">CONTACT US</div>
  </section>

  <h2 class="sec-title" style="top:498px"><strong>PHR</strong> Ecosystem</h2>
  <p class="sec-copy" style="left:140px;top:540px;width:464px">Lorem ipsum dolor sit amet, consectetur adipiscing elit, sed do eiusmod tempor incididunt ut labore et dolore magna aliqua. Ut enim ad minim veniam, quis nostrud</p>
  <div class="cards">
    <div class="card"><div class="pic" role="img" aria-label="Gold coin on stacks of coins" style="background:linear-gradient(135deg,#3a1c4a,#8a5a1a 60%,#d3a040)"></div><h3>Crypto News</h3><p>Lorem ipsum dolor sit consectetur adipiscing elit, sed do incididunt ut labore et dolore</p><div class="more">Read More</div></div>
    <div class="card"><div class="pic" role="img" aria-label="Hands on laptop showing market charts" style="background:linear-gradient(135deg,#6b6e78,#c9ccd4 55%,#3b3d45)"></div><h3>Digital Asset Investing</h3><p>Lorem ipsum dolor sit consectetur adipiscing elit, sed do incididunt ut labore et dolore</p><div class="more">Read More</div></div>
    <div class="card"><div class="pic" role="img" aria-label="Business team meeting around a table" style="background:linear-gradient(135deg,#4a4c52,#9a8f7e 55%,#2c2a28)"></div><h3>Blockchain business solutions</h3><p>Lorem ipsum dolor sit consectetur adipiscing elit, sed do incididunt</p><div class="more">Read More</div></div>
    <div class="card"><div class="pic" role="img" aria-label="Hand touching glowing NFT network interface" style="background:linear-gradient(135deg,#0e2450,#2d6cc0 55%,#0b1a3a)"></div><h3>NFT &nbsp;creative art projects</h3><p>Lorem ipsum dolor sit consectetur adipiscing elit, sed do incididunt ut labore et dolore</p><div class="more">Read More</div></div>
  </div>

  <section class="edu" role="img" aria-label="Faded photo of a person studying at a desk behind blue tint">
    <h2 class="sec-title">Digital Asset <strong>Education</strong></h2>
    <p class="sec-copy" style="left:100px;top:98px;width:544px;color:#fff;font-size:9.5px;line-height:21px">Lorem ipsum dolor sit amet, consectetur adipiscing elit, sed do eiusmod tempor incididunt ut labore et dolore magna aliqua. Ut enim ad minim veniam, quis nostrud exercitation ullamco laboris nisi ut aliquip ex ea commodo consequat. Duis aute irure dolor in reprehenderit in voluptate velit esse cillum</p>
    <div class="btn red" style="left:262px;top:170px;width:120px;height:36px">SIGNUP</div>
    <div class="btn ghost" style="left:388px;top:170px;width:120px;height:36px">BLOG</div>
  </section>

  <h2 class="nft-title"><strong>NFT Virtaul</strong> Module</h2>
  <p class="nft-copy">Lorem ipsum dolor sit amet, consectetur adipiscing elit, sed do eiusmod tempor incididunt ut labore et dolore magna aliqua. Ut enim ad minim veniam, quis nostrud exercitation ullamco laboris nisi ut aliquip ex ea commodo consequat. Duis aute irure reprehenderit in voluptate velit esse cillum dolore eu fugiat nulla pariatur. Excepteur sint occaecat cupidatat non proident, sunt in culpa qui officia deserunt mollit anim id est laborum Lorem ipsum dolor sit amet, consectetur adipiscing elit,</p>
  <div class="btn outline" style="left:69px;top:1412px;width:121px;height:35px">READ MORE</div>
  <div class="abs" style="left:580px;top:1173px;width:118px;height:117px;border:1px solid var(--red)"></div>
  <div class="abs" role="img" aria-label="Person touching a glowing NFT globe interface" style="left:390px;top:1200px;width:283px;height:268px;background:radial-gradient(circle at 35% 50%,#d8f0ff,#7fb8e0 40%,#3c6fa6 75%,#22375a);box-shadow:0 2px 6px rgba(0,0,0,.25)"></div>

  <section class="videos">
    <h2 class="sec-title" style="top:36px">Videos <strong style="color:var(--red)">&amp;</strong> Podcasts</h2>
    <div class="vcard" style="left:69px"><div class="pic" role="img" aria-label="Man working on laptop at home" style="background:linear-gradient(135deg,#8a5048,#c79d86 55%,#4a3430)"><svg class="play" width="30" height="30" viewBox="0 0 30 30"><circle cx="15" cy="15" r="15" fill="#fff"/><path d="M11 8l11 7-11 7z" fill="#1b2340"/></svg></div><h4>Lorem ipsum dolor sit amet, adipiscing elit, sed do Lorem ipsum</h4><p>Lorem ipsum dolor sit amet, adipiscing elit, sed do eiusmod tempor incididunt</p><div class="vmeta"><span class="price">$20.00</span><span class="dots"><b></b><b></b><b></b><b></b></span></div></div>
    <div class="vcard" style="left:274px"><div class="pic" role="img" aria-label="Woman in denim jacket using laptop" style="background:linear-gradient(135deg,#2a3550,#5a6f96 50%,#8a5a40)"><svg class="play" width="30" height="30" viewBox="0 0 30 30"><circle cx="15" cy="15" r="15" fill="#fff"/><path d="M11 8l11 7-11 7z" fill="#1b2340"/></svg></div><h4>Lorem ipsum dolor sit amet, adipiscing elit, sed do Lorem ipsum</h4><p>Lorem ipsum dolor sit amet, adipiscing elit, sed do eiusmod tempor incididunt</p><div class="vmeta"><span class="price">$20.00</span><span class="dots"><b></b><b></b><b></b><b></b></span></div></div>
    <div class="vcard" style="left:479px"><div class="pic" role="img" aria-label="Laptop with floating digital interface icons" style="background:linear-gradient(135deg,#2b2b30,#6a6a72 55%,#1a1a1e)"><svg class="play" width="30" height="30" viewBox="0 0 30 30"><circle cx="15" cy="15" r="15" fill="#fff"/><path d="M11 8l11 7-11 7z" fill="#1b2340"/></svg></div><h4>Lorem ipsum dolor sit amet, adipiscing elit, sed do Lorem ipsum</h4><p>Lorem ipsum dolor sit amet, adipiscing elit, sed do eiusmod tempor incididunt</p><div class="vmeta"><span class="price">$20.00</span><span class="dots"><b></b><b></b><b></b><b></b></span></div></div>
  </section>

  <footer class="footer">
    <div class="fcol" style="left:71px"><h5>QUICK LINKS</h5><ul><li>Home</li><li>About Us</li><li>PHR Ecosystem</li><li>Blog</li><li>Contact</li></ul></div>
    <div class="fcol" style="left:172px"><h5>PHR ECOSYSTEM</h5><ul><li>Crypto News</li><li>Digital asset investing</li><li>Blockchain business solutions</li><li>NFT &nbsp;Creative art Projects</li></ul></div>
    <div class="fcol" style="left:326px;width:160px"><h5>CONTACT US</h5>
      <div class="lab">ADDRESS</div><div class="val"><svg width="7" height="9" viewBox="0 0 7 9"><path d="M3.5 0a3.5 3.5 0 0 0-3.5 3.5C0 6 3.5 9 3.5 9S7 6 7 3.5A3.5 3.5 0 0 0 3.5 0z" fill="currentColor"/></svg><span>Lorem ipsum dolor sit amet, consectetur adipiscing</span></div>
      <div class="lab" style="margin-top:8px">PHONE</div><div class="val"><svg width="8" height="8" viewBox="0 0 8 8"><path d="M1 0h2l1 2-1 1a4 4 0 0 0 2 2l1-1 2 1v2C4 8 0 4 1 0z" fill="currentColor"/></svg>+1 555-010-2040</div>
      <div class="lab" style="margin-top:10px">EMAIL</div><div class="val"><svg width="9" height="7" viewBox="0 0 9 7"><rect width="9" height="7" fill="currentColor"/><path d="M0 0l4.5 4L9 0" stroke="var(--bg)" fill="none"/></svg>hello@pixelharborrangers.example</div>
    </div>
    <div class="fcol" style="left:506px;width:180px"><h5>NEWSLETTER</h5><p style="line-height:14.5px">Lorem ipsum dolor sit amet, consectetur adipiscing elit, sed do eiusmod tempor</p></div>
    <div class="news-input">Enter Email<i></i></div>
    <div class="frule"></div>
    <div class="copy">© 2022 &nbsp; All Rights Reserved</div>
    <div class="pay"><b style="background:#3a5fb0"></b><b style="background:#d8592a"></b><b style="background:#c9c9c9"></b><b style="background:#3f86c8"></b><b style="background:#e9c35a"></b></div>
    <div class="fsocial"><b></b><b></b><b></b><b></b></div>
  </footer>
</div>

<!-- DARK THEME PAGE -->
<div class="page dark">
  <section class="hero">
    <div class="hero-photo" role="img" aria-label="Smiling young man in glasses and denim jacket at a café table with flowers"></div>
    <div class="brand">PixelHarbor Rangers</div>
    <div class="account">
      <span><span class="ring"><svg width="10" height="10" viewBox="0 0 10 10"><circle cx="5" cy="3" r="2.2" fill="#fff"/><path d="M1 10c0-3 8-3 8 0z" fill="#fff"/></svg></span>LOGIN</span>
      <span><span class="ring"><svg width="10" height="10" viewBox="0 0 10 10"><path d="M0 1h2l1.5 5h5L10 3H3" fill="none" stroke="#fff" stroke-width="1.2"/><circle cx="4" cy="8.5" r="1" fill="#fff"/><circle cx="8" cy="8.5" r="1" fill="#fff"/></svg></span>CART</span>
    </div>
    <div class="top-rule"></div>
    <nav class="nav"><a>HOME</a><i>|</i><a>ABOUT US</a><i>|</i><a>PHR ECOSYSTEM</a><i>|</i><a>BLOG</a><i>|</i><a>CONTACT</a></nav>
    <div class="social-mini" style="color:#fff"><b></b><b></b><b></b><b></b></div>
    <div class="hero-band"></div>
    <svg class="arrow" style="left:22px" width="20" height="16" viewBox="0 0 20 16"><path d="M19 8H3M8 3L3 8l5 5" stroke="#fff" stroke-width="2" fill="none"/></svg>
    <svg class="arrow" style="left:700px" width="20" height="16" viewBox="0 0 20 16"><path d="M1 8h16M12 3l5 5-5 5" stroke="#fff" stroke-width="2" fill="none"/></svg>
    <div class="hero-title">PixelHarbor Rangers</div>
    <p class="hero-copy">Lorem ipsum dolor sit amet, consectetur adipiscing elit, sed do eiusmod tempor incididunt ut labore et dolore magna aliqua.</p>
    <div class="btn red" style="left:425px;top:390px;width:120px;height:36px">GET STARTED</div>
    <div class="btn ghost" style="left:551px;top:390px;width:120px;height:36px">CONTACT US</div>
  </section>

  <h2 class="sec-title" style="top:498px"><strong>PHR</strong> Ecosystem</h2>
  <p class="sec-copy" style="left:140px;top:540px;width:464px">Lorem ipsum dolor sit amet, consectetur adipiscing elit, sed do eiusmod tempor incididunt ut labore et dolore magna aliqua. Ut enim ad minim veniam, quis nostrud</p>
  <div class="pixel-art" role="img" aria-label="Faint pixel-art decoration" style="left:606px;top:505px;width:50px;height:56px"></div>
  <div class="pixel-art" role="img" aria-label="Faint pixel-art decoration" style="left:678px;top:488px;width:50px;height:56px"></div>
  <div class="cards">
    <div class="card"><div class="pic" role="img" aria-label="Gold coin on stacks of coins" style="background:linear-gradient(135deg,#3a1c4a,#8a5a1a 60%,#d3a040)"></div><h3>Crypto News</h3><p>Lorem ipsum dolor sit consectetur adipiscing elit, sed do incididunt ut labore et dolore</p><div class="more">Read More</div></div>
    <div class="card"><div class="pic" role="img" aria-label="Hands on laptop showing market charts" style="background:linear-gradient(135deg,#6b6e78,#c9ccd4 55%,#3b3d45)"></div><h3>Digital Asset Investing</h3><p>Lorem ipsum dolor sit consectetur adipiscing elit, sed do incididunt ut labore et dolore</p><div class="more">Read More</div></div>
    <div class="card"><div class="pic" role="img" aria-label="Business team meeting around a table" style="background:linear-gradient(135deg,#4a4c52,#9a8f7e 55%,#2c2a28)"></div><h3>Blockchain business solutions</h3><p>Lorem ipsum dolor sit consectetur adipiscing elit, sed do incididunt</p><div class="more">Read More</div></div>
    <div class="card"><div class="pic" role="img" aria-label="Hand touching glowing NFT network interface" style="background:linear-gradient(135deg,#0e2450,#2d6cc0 55%,#0b1a3a)"></div><h3>NFT &nbsp;creative art projects</h3><p>Lorem ipsum dolor sit consectetur adipiscing elit, sed do incididunt ut labore et dolore</p><div class="more">Read More</div></div>
  </div>

  <section class="edu" role="img" aria-label="Faded photo of a person studying at a desk behind blue tint">
    <h2 class="sec-title">Digital Asset <strong>Education</strong></h2>
    <p class="sec-copy" style="left:100px;top:98px;width:544px;color:#fff;font-size:9.5px;line-height:21px">Lorem ipsum dolor sit amet, consectetur adipiscing elit, sed do eiusmod tempor incididunt ut labore et dolore magna aliqua. Ut enim ad minim veniam, quis nostrud exercitation ullamco laboris nisi ut aliquip ex ea commodo consequat. Duis aute irure dolor in reprehenderit in voluptate velit esse cillum</p>
    <div class="btn red" style="left:262px;top:170px;width:120px;height:36px">SIGNUP</div>
    <div class="btn ghost" style="left:388px;top:170px;width:120px;height:36px">BLOG</div>
  </section>

  <div class="abs" role="img" aria-label="Faint pixel-art arcade game-over screen" style="left:0;top:1300px;width:225px;height:222px;background:linear-gradient(180deg,#0a0f2a,#101a4a 60%,#060a1c);opacity:.8"></div>
  <h2 class="nft-title"><strong>NFT Virtaul</strong> Module</h2>
  <p class="nft-copy">Lorem ipsum dolor sit amet, consectetur adipiscing elit, sed do eiusmod tempor incididunt ut labore et dolore magna aliqua. Ut enim ad minim veniam, quis nostrud exercitation ullamco laboris nisi ut aliquip ex ea commodo consequat. Duis aute irure reprehenderit in voluptate velit esse cillum dolore eu fugiat nulla pariatur. Excepteur sint occaecat cupidatat non proident, sunt in culpa qui officia deserunt mollit anim id est laborum Lorem ipsum dolor sit amet, consectetur adipiscing elit,</p>
  <div class="btn outline" style="left:69px;top:1412px;width:121px;height:35px">READ MORE</div>
  <div class="abs" style="left:580px;top:1173px;width:118px;height:117px;border:1px solid var(--red)"></div>
  <div class="abs" role="img" aria-label="Person touching a glowing NFT globe interface" style="left:390px;top:1200px;width:283px;height:268px;background:radial-gradient(circle at 35% 50%,#d8f0ff,#7fb8e0 40%,#3c6fa6 75%,#22375a)"></div>

  <section class="videos">
    <h2 class="sec-title" style="top:36px">Videos <strong>&amp;</strong> Podcasts</h2>
    <div class="vcard" style="left:69px"><div class="pic" role="img" aria-label="Man working on laptop at home" style="background:linear-gradient(135deg,#8a5048,#c79d86 55%,#4a3430)"><svg class="play" width="30" height="30" viewBox="0 0 30 30"><circle cx="15" cy="15" r="15" fill="#fff"/><path d="M11 8l11 7-11 7z" fill="#1b2340"/></svg></div><h4>Lorem ipsum dolor sit amet, adipiscing elit, sed do Lorem ipsum</h4><p>Lorem ipsum dolor sit amet, adipiscing elit, sed do eiusmod tempor incididunt</p><div class="vmeta"><span class="price">$20.00</span><span class="dots"><b></b><b></b><b></b><b></b></span></div></div>
    <div class="vcard" style="left:274px"><div class="pic" role="img" aria-label="Woman in denim jacket using laptop" style="background:linear-gradient(135deg,#2a3550,#5a6f96 50%,#8a5a40)"><svg class="play" width="30" height="30" viewBox="0 0 30 30"><circle cx="15" cy="15" r="15" fill="#fff"/><path d="M11 8l11 7-11 7z" fill="#1b2340"/></svg></div><h4>Lorem ipsum dolor sit amet, adipiscing elit, sed do Lorem ipsum</h4><p>Lorem ipsum dolor sit amet, adipiscing elit, sed do eiusmod tempor incididunt</p><div class="vmeta"><span class="price">$20.00</span><span class="dots"><b></b><b></b><b></b><b></b></span></div></div>
    <div class="vcard" style="left:479px"><div class="pic" role="img" aria-label="Laptop with floating digital interface icons" style="background:linear-gradient(135deg,#2b2b30,#6a6a72 55%,#1a1a1e)"><svg class="play" width="30" height="30" viewBox="0 0 30 30"><circle cx="15" cy="15" r="15" fill="#fff"/><path d="M11 8l11 7-11 7z" fill="#1b2340"/></svg></div><h4>Lorem ipsum dolor sit amet, adipiscing elit, sed do Lorem ipsum</h4><p>Lorem ipsum dolor sit amet, adipiscing elit, sed do eiusmod tempor incididunt</p><div class="vmeta"><span class="price">$20.00</span><span class="dots"><b></b><b></b><b></b><b></b></span></div></div>
  </section>

  <footer class="footer">
    <div class="fcol" style="left:71px"><h5>QUICK LINKS</h5><ul><li>Home</li><li>About Us</li><li>PHR Ecosystem</li><li>Blog</li><li>Contact</li></ul></div>
    <div class="fcol" style="left:172px"><h5>PHR ECOSYSTEM</h5><ul><li>Crypto News</li><li>Digital asset investing</li><li>Blockchain business solutions</li><li>NFT &nbsp;Creative art Projects</li></ul></div>
    <div class="fcol" style="left:326px;width:160px"><h5>CONTACT US</h5>
      <div class="lab">ADDRESS</div><div class="val"><svg width="7" height="9" viewBox="0 0 7 9"><path d="M3.5 0a3.5 3.5 0 0 0-3.5 3.5C0 6 3.5 9 3.5 9S7 6 7 3.5A3.5 3.5 0 0 0 3.5 0z" fill="currentColor"/></svg><span>Lorem ipsum dolor sit amet, consectetur adipiscing</span></div>
      <div class="lab" style="margin-top:8px">PHONE</div><div class="val"><svg width="8" height="8" viewBox="0 0 8 8"><path d="M1 0h2l1 2-1 1a4 4 0 0 0 2 2l1-1 2 1v2C4 8 0 4 1 0z" fill="currentColor"/></svg>+1 555-010-2040</div>
      <div class="lab" style="margin-top:10px">EMAIL</div><div class="val"><svg width="9" height="7" viewBox="0 0 9 7"><rect width="9" height="7" fill="currentColor"/><path d="M0 0l4.5 4L9 0" stroke="var(--bg)" fill="none"/></svg>hello@pixelharborrangers.example</div>
    </div>
    <div class="fcol" style="left:506px;width:180px"><h5>NEWSLETTER</h5><p style="line-height:14.5px">Lorem ipsum dolor sit amet, consectetur adipiscing elit, sed do eiusmod tempor</p></div>
    <div class="news-input"><i></i></div>
    <div class="frule"></div>
    <div class="copy">© 2022 &nbsp; All Rights Reserved</div>
    <div class="pay"><b style="background:#3a5fb0"></b><b style="background:#d8592a"></b><b style="background:#c9c9c9"></b><b style="background:#3f86c8"></b><b style="background:#e9c35a"></b></div>
    <div class="fsocial"><b></b><b></b><b></b><b></b></div>
  </footer>
</div>

</body>
</html>
```